Specialised investor in e-mobility and energy wants business card design

We need a business card design that fits our existing corporate design. <The look and feel must be 'sharp'/'clean', dynamic, communicate momentum, professionalism etc (as one would imagine from a firm in the financial sector). We like the idea of a reverse-side of the card that includes the logo, and the name and contact details on the other. We expect the deliverable to be whatever format might be required to be able to get cards printed directly by a service such as kelmo press. Our website is www.zub.capital

```html
<!DOCTYPE html>
<html lang="en">
<head>
<meta charset="utf-8">
<title>ZUB Capital – Business Card</title>
<link rel="stylesheet" href="https://fonts.googleapis.com/css2?family=Montserrat:wght@400;500;700&display=swap">
<style>
  :root {
    --forest: #2e4c23;
    --leaf: #86b34a;
    --paper: #ffffff;
    --backdrop: #e9ebe6;
    --ink-soft: #f2f4ef;
  }
  * { margin: 0; padding: 0; box-sizing: border-box; }
  html, body { width: 900px; height: 1200px; overflow: hidden; }
  body {
    background: var(--backdrop);
    font-family: "Montserrat", Arial, sans-serif;
    position: relative;
  }
  .card {
    position: absolute;
    left: 80px;
    width: 742px;
    height: 440px;
    border-radius: 32px;
    overflow: hidden;
  }
  .card--front { top: 132px; background: var(--paper); }
  .card--back { top: 640px; background: var(--forest); }

  .card__swoosh { position: absolute; inset: 0; width: 100%; height: 100%; }

  .wordmark {
    position: absolute;
    font-weight: 500;
    letter-spacing: 0.5px;
    white-space: nowrap;
    line-height: 1;
  }
  .card--front .wordmark { left: 22px; top: 76px; font-size: 58px; color: var(--forest); }
  .card--back .wordmark {
    left: 0; right: 0; top: 170px;
    text-align: center; font-size: 82px; color: var(--ink-soft);
  }

  .holder { position: absolute; left: 37px; top: 278px; }
  .holder__name { font-size: 26px; font-weight: 700; color: var(--leaf); }
  .holder__role { font-size: 16px; color: var(--paper); margin-top: 2px; }

  .contacts { position: absolute; left: 37px; top: 352px; list-style: none; }
  .contacts li {
    display: flex; align-items: center; gap: 12px;
    font-size: 15.5px; color: var(--paper); height: 22.5px;
  }
  .contacts svg { width: 13px; height: 13px; fill: var(--leaf); flex: none; }
</style>
</head>
<body>

<section class="card card--front">
  <svg class="card__swoosh" viewBox="0 0 742 440" aria-hidden="true">
    <path d="M0,250 C200,196 470,196 742,426 V440 H0 Z" fill="var(--forest)"/>
    <path d="M40,221 C260,196 520,210 742,398 V418 C520,226 270,204 40,221 Z" fill="var(--leaf)"/>
  </svg>

  <div class="wordmark">ZUB Capital</div>

  <div class="holder">
    <div class="holder__name">Mark Hollenby</div>
    <div class="holder__role">Owner</div>
  </div>

  <ul class="contacts">
    <li>
      <svg viewBox="0 0 16 16"><path d="M2,6 C2,3 5,2 8,2 C11,2 14,3 14,6 H11 V5 H5 V6 Z M3,7 H13 L14,14 H2 Z"/></svg>
      +41 79518 4407
    </li>
    <li>
      <svg viewBox="0 0 16 16"><path d="M1,3 H15 V4 L8,9 L1,4 Z M1,6 L8,11 L15,6 V13 H1 Z"/></svg>
      mark@zub.capital
    </li>
    <li>
      <svg viewBox="0 0 16 16"><circle cx="8" cy="8" r="7"/></svg>
      www.zub.capital.com
    </li>
  </ul>
</section>

<section class="card card--back">
  <div class="wordmark">ZUB Capital</div>
</section>

</body>
</html>
```